TEBSIRK HOA Portal Site for Public

Clean up and organize current website; need website to look good and functional; this is a HOA (homeowner association management) website where homeowners can login and pay their bill, general information about a HOA, monthly newsletter page.
Competitors:
https://quillmarsh.example/
https://dorvinpalms.example/
https://www.kelbrookhomes.example/nevada
http://www.tpw-hoa.example/

Target Market(s)

homeowners

Industry/Entity Type

Real Estate

Coding

Coded - Design and coding required

Number of Pages Required

5+ page

Font styles to use
Serif

Colors
0292cd
33a6d7
e667a6
e34297

Requirements
Must have
• login to pay
• services page
• contact us
• order resale package
Nice to have
• page why an HOA would contract us

```html
<!DOCTYPE html>
<html lang="en">
<head>
<meta charset="utf-8">
<title>TEBSIRK HOA – Homeowner Association Management</title>
<link href="https://fonts.googleapis.com/css2?family=Mulish:wght@300;400;600&family=Roboto:wght@300;400;700;900&family=Oswald:wght@400;500&display=swap" rel="stylesheet">
<style>
:root{
  --blue:#0292cd;
  --blue-soft:#33a6d7;
  --pink:#e667a6;
  --pink-deep:#e34297;
  --dark:#2b2c30;
  --text:#333;
  --muted:#8a8a8a;
  --line:#e6e6e6;
  --white:#fff;
}
*{margin:0;padding:0;box-sizing:border-box}
html,body{width:1200px;height:3531px;overflow:hidden}
body{position:relative;font-family:"Mulish",sans-serif;color:var(--text);background:var(--white)}
.abs{position:absolute}
a{color:inherit;text-decoration:none}

/* Hero */
.hero{left:0;top:0;width:1200px;height:573px;background:linear-gradient(180deg,#6d6d70 0%,#8a8680 45%,#6e6a58 100%)}
.hero-shade{left:0;top:0;width:1200px;height:573px;background:rgba(40,40,45,.35)}
.logo{font-family:"Oswald",sans-serif;font-weight:500;letter-spacing:1px}
.hero .logo{left:75px;top:30px;font-size:35px;color:var(--white)}
.nav{left:357px;top:40px;display:flex;gap:25px;font-size:16px;color:var(--white)}
.nav .active{color:var(--pink-deep);position:relative}
.nav .active::after{content:"";position:absolute;left:50%;top:30px;margin-left:-6px;border:6px solid transparent;border-bottom:9px solid var(--pink-deep);border-top:0}
.search{left:1102px;top:41px}
.hero-title{left:0;width:1200px;top:208px;text-align:center;font-family:"Roboto",sans-serif;font-weight:900;font-size:50px;line-height:62px;text-transform:uppercase}
.hero-title .l1{color:var(--blue-soft)}
.hero-title .l2{color:var(--pink)}
.hero-lead{left:0;width:1200px;top:335px;text-align:center;color:var(--white);font-size:19px;line-height:27px}
.arrow-btn{width:52px;height:52px;border-radius:50%;display:flex;align-items:center;justify-content:center}
.arrow-prev{left:51px;top:270px;background:var(--blue)}
.arrow-next{left:1097px;top:270px;background:#d9d9d9}

/* Subscribe */
.subscribe{left:185px;top:500px}
.subscribe-title{left:0;width:1200px;top:548px;text-align:center;color:var(--white);font-family:"Roboto",sans-serif;font-weight:300;font-size:27px}
.email-field{left:298px;top:607px;width:603px;height:62px;border-radius:31px;background:var(--white);border:3px solid var(--white)}
.email-field span{position:absolute;left:22px;top:20px;font-size:16px;color:#777}
.submit{left:740px;top:612px;width:158px;height:52px;border-radius:26px;background:linear-gradient(90deg,var(--blue),var(--pink-deep));color:var(--white);font-size:19px;display:flex;align-items:center;justify-content:center;gap:10px}

/* Offer */
.offer-frame{left:77px;top:791px;width:417px;height:521px;border:10px solid;border-image:linear-gradient(180deg,var(--blue),var(--pink-deep)) 1;border-right:none;border-bottom-width:10px}
.offer-photo{left:119px;top:843px;width:468px;height:532px;background:linear-gradient(160deg,#f1efec,#d9cfc3 60%,#b89a78)}
.offer-title{left:638px;top:838px;font-family:"Roboto",sans-serif;font-weight:300;font-size:48px;color:#222}
.offer-list{left:638px;top:916px;width:485px;list-style:none;font-size:14.5px;line-height:20.5px;color:var(--muted);font-weight:300}
.offer-list li{margin-bottom:16px}
.read-more{display:flex;align-items:center;gap:14px;font-size:19px;color:var(--blue)}
.offer-more{left:638px;top:1351px}

/* Partners */
.partner-line{top:1484px;height:1px;background:var(--line)}
.partner-pill{left:521px;top:1459px;width:156px;height:51px;border-radius:26px;background:linear-gradient(90deg,var(--blue),var(--pink-deep));color:var(--white);font-family:"Roboto",sans-serif;font-size:18px;display:flex;align-items:center;justify-content:center}
.partner-badge{top:1553px;height:28px;border-radius:4px;background:#d5d5d5}

/* Services */
.services{left:0;top:1677px;width:1200px;height:822px;background:var(--dark)}
.services-title{left:0;width:1200px;top:1752px;text-align:center;color:var(--white);font-family:"Roboto",sans-serif;font-weight:300;font-size:48px}
.card-frame{width:448px;height:395px;background:linear-gradient(180deg,var(--blue) 0%,var(--pink-deep) 100%)}
.card{width:469px;height:536px;background:var(--white)}
.card-photo{position:absolute;left:0;top:0;width:469px;height:313px}
.card h3{position:absolute;left:33px;top:338px;width:410px;font-family:"Roboto",sans-serif;font-weight:400;font-size:25px;line-height:31px;color:#222}
.card p{position:absolute;left:33px;width:415px;font-size:14.5px;line-height:26px;color:var(--muted);font-weight:300}
.card .read-more{position:absolute;left:33px;top:481px}

/* Feedback */
.feedback{left:0;top:2499px;width:1200px;height:689px;background:linear-gradient(100deg,#2ea6dc 0%,#7f86cc 50%,#e657a3 100%)}
.feedback-title{left:0;width:1200px;top:2575px;text-align:center;color:var(--white);font-family:"Roboto",sans-serif;font-weight:300;font-size:50px}
.quote{left:245px;top:2798px;width:710px;text-align:center;color:var(--white);font-size:18.5px;line-height:26px}
.qmark{font-family:"Roboto",sans-serif;font-weight:700;font-size:54px;color:var(--white);line-height:1}
.client{left:0;width:1200px;top:2936px;text-align:center;color:var(--white);font-family:"Roboto",sans-serif;font-size:18px}
.client-role{left:0;width:1200px;top:2968px;text-align:center;color:var(--white);font-size:14px}

/* Footer */
.footer-logo{left:0;width:1200px;top:3240px;text-align:center;font-size:36px;color:#222}
.footer-nav{left:0;width:1200px;top:3308px;text-align:center;font-size:14.5px;color:#888}
.footer-nav span{margin:0 12px}
.social{top:3346px;width:42px;height:42px;border-radius:50%}
.footer-rule{left:0;top:3448px;width:1200px;height:1px;background:var(--line)}
.copyright{left:0;width:1200px;top:3476px;text-align:center;font-size:14px;color:#999}
.copyright b{color:#444;font-weight:600}
</style>
</head>
<body>

<!-- Hero -->
<div class="abs hero" role="img" aria-label="Suburban house with a for-sale sign in the front yard"></div>
<div class="abs hero-shade"></div>
<div class="abs logo">TEBSIRK HOA</div>
<nav class="abs nav">
  <a class="active" href="#">Home</a>
  <a href="#">Services</a>
  <a href="#">Why an HOA would contract us</a>
  <a href="#">Order resale package</a>
  <a href="#">Contact Us</a>
</nav>
<svg class="abs search" width="20" height="20" viewBox="0 0 20 20" fill="none" stroke="#fff" stroke-width="2"><circle cx="8" cy="8" r="6.5"/><line x1="13" y1="13" x2="19" y2="19"/></svg>
<h1 class="abs hero-title"><span class="l1">Homeowner Association</span><br><span class="l2">Management</span></h1>
<p class="abs hero-lead">Lorem ipsum dolor sit amet, consectetur adipiscing elit, sed do eiusmod tempor<br>incididunt ut labore et dolore magna aliqua.</p>
<div class="abs arrow-btn arrow-prev"><svg width="14" height="14" viewBox="0 0 14 14" fill="none" stroke="#fff" stroke-width="2.5"><polyline points="9,2 4,7 9,12"/></svg></div>
<div class="abs arrow-btn arrow-next"><svg width="14" height="14" viewBox="0 0 14 14" fill="none" stroke="#222" stroke-width="2.5"><polyline points="5,2 10,7 5,12"/></svg></div>

<!-- Subscribe -->
<svg class="abs subscribe" width="830" height="210" viewBox="0 0 830 210">
  <path d="M40 0 H790 Q830 0 825 40 L800 175 Q793 209 755 209 H75 Q40 209 33 175 L5 40 Q0 0 40 0 Z" fill="var(--dark)"/>
</svg>
<div class="abs subscribe-title">Subscribe To Email List</div>
<div class="abs email-field"><span>Your e-Mail</span></div>
<div class="abs submit">
  <svg width="24" height="22" viewBox="0 0 24 22" fill="none" stroke="#fff" stroke-width="1.6"><path d="M1 10 L23 1 L17 21 L11 13 Z"/><line x1="11" y1="13" x2="23" y2="1"/></svg>
  Submit
</div>

<!-- What We Offer -->
<div class="abs offer-frame"></div>
<div class="abs offer-photo" role="img" aria-label="Family meeting an agent in the entry hall of an empty home"></div>
<h2 class="abs offer-title">What We Offer</h2>
<ul class="abs offer-list">
  <li>Accessible, licensed Association Managers</li>
  <li>24 hour Web site access: online account information</li>
  <li>24 hour emergency service</li>
  <li>Provide monthly financial reports to the Board of Directors</li>
  <li>Read, study and understand all governing documents of the Association. Correspond with members in violation of the CC&amp;Rs, By-laws, Rules &amp; Regulations and report the status of all noncompliance to the Board of Directors in a timely manner.</li>
  <li>Act as the custodian of the corporate records. Coordinate preparing annual tax returns for the Association.</li>
  <li>Preparation and scheduling for Board meetings and annual membership meetings.</li>
  <li>Monitor delinquencies; send late notices and present problem accounts to the Board of Directors with recommendations for further action.</li>
</ul>
<a class="abs read-more offer-more" href="#">Read More
  <svg width="32" height="10" viewBox="0 0 32 10" fill="none" stroke="var(--pink-deep)" stroke-width="2"><line x1="0" y1="5" x2="30" y2="5"/><polyline points="25,1 30,5 25,9"/></svg></a>

<!-- Partners -->
<div class="abs partner-line" style="left:77px;width:420px"></div>
<div class="abs partner-line" style="left:701px;width:422px"></div>
<div class="abs partner-pill">Our Partners</div>
<div class="abs partner-badge" style="left:77px;width:176px"></div>
<div class="abs partner-badge" style="left:293px;width:128px"></div>
<div class="abs partner-badge" style="left:456px;width:100px"></div>
<div class="abs partner-badge" style="left:603px;width:127px"></div>
<div class="abs partner-badge" style="left:772px;width:138px"></div>
<div class="abs partner-badge" style="left:945px;width:177px"></div>

<!-- Services -->
<section class="abs services"></section>
<h2 class="abs services-title">Our Services</h2>
<div class="abs card-frame" style="left:77px;top:1854px"></div>
<div class="abs card" style="left:97px;top:1874px">
  <div class="card-photo" role="img" aria-label="Agent reviewing documents with an older couple in a kitchen" style="background:linear-gradient(150deg,#e9e2d6,#b9a88f 55%,#4b5a86)"></div>
  <h3>Association Management Services</h3>
  <p style="top:386px">Lorem ipsum dolor sit amet, consectetur adipiscing elit, sed do thereof eiusmod tempor incididunt ut labore et dolore to magna aliqua. Ut enim ad minim veniam.</p>
  <a class="read-more" href="#">Read More <svg width="32" height="10" viewBox="0 0 32 10" fill="none" stroke="var(--pink-deep)" stroke-width="2"><line x1="0" y1="5" x2="30" y2="5"/><polyline points="25,1 30,5 25,9"/></svg></a>
</div>
<div class="abs card-frame" style="left:633px;top:1854px"></div>
<div class="abs card" style="left:654px;top:1874px">
  <div class="card-photo" role="img" aria-label="Model house on a desk beside people signing paperwork" style="background:linear-gradient(150deg,#d7dce3,#9aa7b8 55%,#c99a55)"></div>
  <h3>TEBSIRK manages communities throughout Southern Nevada</h3>
  <p style="top:417px">Lorem ipsum dolor sit amet, consectetur adipiscing elit, sed do thereof eiusmod tempor incididunt ut labore.</p>
  <a class="read-more" href="#">Read More <svg width="32" height="10" viewBox="0 0 32 10" fill="none" stroke="var(--pink-deep)" stroke-width="2"><line x1="0" y1="5" x2="30" y2="5"/><polyline points="25,1 30,5 25,9"/></svg></a>
</div>

<!-- Clients Feedback -->
<section class="abs feedback" role="img" aria-label="Family relaxing at home, tinted blue to pink"></section>
<h2 class="abs feedback-title">Clients Feedback</h2>
<svg class="abs" style="left:366px;top:2678px" width="468" height="363" viewBox="0 0 468 363" fill="none" stroke="rgba(255,255,255,.6)" stroke-width="5">
  <polyline points="2.5,82 2.5,2.5 465.5,2.5 465.5,82"/>
  <polyline points="2.5,281 2.5,360.5 465.5,360.5 465.5,281"/>
</svg>
<div class="abs qmark" style="left:195px;top:2798px">&ldquo;</div>
<p class="abs quote">Lorem ipsum dolor sit amet, consectetur adipiscing elit, sed do eiusmod tempor incididunt ut labore et dolore magna aliqua. Ut enim ad minim veniam, quis nostrud exercitation ullamco laboris nisi ut aliquip ex ea velit esse cillum dolore eu fugiat nulla pariatur.</p>
<div class="abs qmark" style="left:716px;top:2880px">&rdquo;</div>
<div class="abs client">- Client Name</div>
<div class="abs client-role">Lorem Ipsum</div>
<svg class="abs" style="left:565px;top:3083px" width="70" height="20" viewBox="0 0 70 20">
  <circle cx="9" cy="10" r="4.5" fill="#fff"/>
  <circle cx="35" cy="10" r="8" fill="none" stroke="#fff" stroke-width="1.5"/>
  <circle cx="35" cy="10" r="4.5" fill="#fff"/>
  <circle cx="61" cy="10" r="4.5" fill="#fff"/>
</svg>

<!-- Footer -->
<div class="abs logo footer-logo">TEBSIRK HOA</div>
<nav class="abs footer-nav">
  <a href="#">Home</a><span>|</span><a href="#">Services</a><span>|</span><a href="#">Why an HOA would contract us</a><span>|</span><a href="#">Order resale package</a><span>|</span><a href="#">Contact Us</a>
</nav>
<a class="abs social" href="#" aria-label="Social profile one" style="left:509px;background:#3b5998"></a>
<a class="abs social" href="#" aria-label="Social profile two" style="left:556px;background:#1da1f2"></a>
<a class="abs social" href="#" aria-label="Social profile three" style="left:602px;background:#d23e2b"></a>
<a class="abs social" href="#" aria-label="Social profile four" style="left:649px;background:#0073b1"></a>
<div class="abs footer-rule"></div>
<p class="abs copyright">Copyright © <b>TEBSIRK HOA</b> - 2019 . All Right Reserved</p>

</body>
</html>
```